Business Card for Multi-Brand Sportswear Company

We are looking for a business card which represents our company and the multiple brands within it.

The company: Fen Athletics (LTD)
The brands: Fen, TavaPuni, ElmStretch, Grit and Rain

Employees using these cards would be representing Fen Athletics, rather than any of the individual brands. You will see a current design within the uploaded files, to give some inspiration. The actual text of the brands is not necessary, but the logos should be on there is some format.

Our creative minds on this are stretched, so we are looking for someone to make this their own, and show us what a good business card should look like.

We may like to get these printed with spot gloss, so keep that in mind with your designs.

www.fenathletics.co.uk

Industry/Entity Type

Business

Contact Information for Business Card

Leo Pemberton-Hale
Operations Manager
(+44) 1632 960 418
Leo@fenathletics.co.uk
www.fenathletics.co.uk

Font styles to use
Sans Serif
Other font styles liked:
• Eurostile

Colors
ffffff

Requirements
Nice to have
• Dark (black) background

```html
<!DOCTYPE html>
<html lang="en">
<head>
<meta charset="utf-8">
<title>Fen Athletics – Business Card</title>
<link rel="stylesheet" href="https://fonts.googleapis.com/css2?family=Exo+2:wght@400;500;600;700&display=swap">
<style>
  :root {
    --backdrop: #3b3b3b;
    --card-light: #ffffff;
    --card-dark: #000000;
    --ink: #111111;
    --ink-soft: #555555;
    --accent: #e3202a;
    --rule: #222222;
    --brand-grey: #9a9a9a;
    --brand-plum: #5f4e5c;
    --on-dark: #ffffff;
  }
  * { box-sizing: border-box; margin: 0; padding: 0; }
  html, body {
    width: 1105px; height: 1200px; overflow: hidden;
    background: var(--backdrop);
    font-family: "Exo 2", sans-serif;
  }
  .canvas { position: relative; width: 1105px; height: 1200px; }

  .card {
    position: absolute; left: 196px; width: 720px; height: 410px;
  }
  .card--front { top: 146px; background: var(--card-light); color: var(--ink); }
  .card--back  { top: 602px; background: var(--card-dark); color: var(--on-dark); }

  /* Front */
  .wordmark {
    position: absolute; top: 70px; left: 0; right: 0; text-align: center;
  }
  .wordmark__name {
    font-size: 52px; font-weight: 600; letter-spacing: 2px; line-height: 1;
    color: var(--ink); text-transform: uppercase;
  }
  .wordmark__tagline {
    margin-top: 8px; font-size: 14px; letter-spacing: 3px; color: var(--ink-soft);
  }
  .person { position: absolute; top: 208px; left: 0; right: 0; text-align: center; }
  .person__name {
    font-size: 26px; font-weight: 700; color: var(--accent); letter-spacing: 0.5px;
    text-transform: uppercase;
  }
  .person__role { margin-top: 4px; font-size: 19px; color: var(--ink); }

  .rule { position: absolute; left: 50px; right: 50px; height: 1.5px; background: var(--rule); }
  .rule--top { top: 278px; }
  .rule--bottom { top: 351px; }

  .contact {
    position: absolute; top: 290px; left: 50px; right: 50px;
    display: flex; justify-content: space-between;
    font-size: 19px; line-height: 28px; color: var(--ink-soft);
  }
  .contact__item { display: flex; align-items: center; gap: 10px; }
  .contact__icon { width: 16px; height: 16px; fill: var(--accent); }
  .contact__address { text-align: right; }

  .website {
    position: absolute; left: 0; right: 0; text-align: center;
    letter-spacing: 6px; font-size: 18px;
  }
  .card--front .website { top: 366px; color: var(--ink-soft); }
  .card--back .website { top: 340px; color: var(--on-dark); font-style: italic; letter-spacing: 10px; }

  /* Back */
  .brand-row {
    position: absolute; top: 196px; left: 0; right: 0;
    display: flex; justify-content: center; align-items: center; gap: 34px;
  }
  .brand { display: flex; align-items: center; gap: 8px; font-size: 24px; font-weight: 600; }
  .brand__mark { width: 14px; height: 14px; }
  .brand--fen { color: var(--on-dark); font-size: 34px; }
  .brand--tava { color: var(--brand-grey); }
  .brand--tava .brand__mark { border-radius: 50%; border: 3px solid var(--brand-grey); }
  .brand--elm { color: var(--brand-grey); }
  .brand--elm .brand__mark { background: var(--brand-plum); }
  .brand--grit { color: var(--accent); }
</style>
</head>
<body>
<main class="canvas">
  <section class="card card--front" aria-label="Card front">
    <div class="wordmark">
      <div class="wordmark__name">Fen Athletics</div>
      <div class="wordmark__tagline">PERFORMANCE WEAR</div>
    </div>
    <div class="person">
      <div class="person__name">Leo Pemberton-Hale</div>
      <div class="person__role">Operations Manager</div>
    </div>
    <div class="rule rule--top"></div>
    <div class="contact">
      <div class="contact__list">
        <div class="contact__item">
          <svg class="contact__icon" viewBox="0 0 24 24" aria-hidden="true"><path d="M6.6 10.8a15.1 15.1 0 0 0 6.6 6.6l2.2-2.2c.3-.3.7-.4 1-.2 1.1.4 2.3.6 3.6.6.6 0 1 .4 1 1V20c0 .6-.4 1-1 1A17 17 0 0 1 3 4c0-.6.4-1 1-1h3.5c.6 0 1 .4 1 1 0 1.3.2 2.5.6 3.6.1.3 0 .7-.2 1z"/></svg>
          <span>(+44) 1632 960 418</span>
        </div>
        <div class="contact__item">
          <svg class="contact__icon" viewBox="0 0 24 24" aria-hidden="true"><path d="M2 5h20v14H2z"/><path d="M3 6l9 7 9-7" fill="none" stroke="#fff" stroke-width="1.6"/></svg>
          <span>Leo@fenathletics.co.uk</span>
        </div>
      </div>
      <div class="contact__address">
        <div>Ashby Court, Millbrook</div>
        <div>Harlow, ZZ1 4QT</div>
      </div>
    </div>
    <div class="rule rule--bottom"></div>
    <div class="website">www.fenathletics.co.uk</div>
  </section>

  <section class="card card--back" aria-label="Card back">
    <div class="brand-row">
      <div class="brand brand--fen">Fen</div>
      <div class="brand brand--tava"><span class="brand__mark"></span>TavaPuni</div>
      <div class="brand brand--elm"><span class="brand__mark"></span>ElmStretch</div>
      <div class="brand brand--grit">Grit and Rain</div>
    </div>
    <div class="website">www.fenathletics.co.uk</div>
  </section>
</main>
</body>
</html>
```